Doctor to Patient Management Website

I need a design for a health management website that connects doctors to patients. The website will consist of: A main page mainly describing our goal, services, and initiatives towards (Who we are AKA "About Us", Our services, Contact Us, Quick Links for health tips, Language selection, Find a doctor, search bar, Member Login Section, small glossary section below with links to all entities mentioned prior, Help section (Helpful tips and tutorials, Used to request help from admin, customer service, to resolve issues or get assistance). A profile page with two types:1) Doctor Profile: Doctor Personal info (First, Last, Middle Name, Title), Clinic, Hospital Info, Department, Credentials, Years of Experience, Patients rating, #Patients seen during the current week, #Patients seen in total, Picture, Link to email doctor, Link to print doctor's profile). Tabs for "About Me", "Contact Info", "Ratings & Comments", "Documents" (To be downloaded and uploaded by patient), "Patients (List of Patients alphabetical order by name)", "Calendar" (to see doctor's availability for booking) underneath all links. 2) Patient profile: About me, Personal Info, Height, Weight, Blood Type, Age, DOB, Name, etc..., Message and email link.Picture of patient with menu made of "Personal Data", "Biometrics", "Allergies", "Illnesses", "Medications", "Medical Procedures", "Doctors" treating the patient, "Documents" (To be downloaded and uploaded by patient). Underneath all, other patients he or she is related to (For example: family member, so patient can't connect to other patients who are family members)3) Login section: New Users will have option to register using:First Name (Required), Last Name, Middle (not required), Address (Not required), City (Required), Country (Required), Email (Not required), Phone Number (Required), Choose UserName, Password, Account Type (Doctor or Patient). Once registered, they will log in using UserName, Password, and Account_Type.Curent Users will log in using UserName, Password, and Account_Type and option to retrieve username or password.Pages to include (Login Page - Registration Page - Retrieve Username and Reset Password Page)Please see link below:https://plumcrate-adwerks.net/importance-claiming-vantorix-quibble-zarn/Pictures are attached to this project as an inspirationFYI: Dummy text can be used to fill in the business, services, and descriptive information. Feel free to include your own ideas in the layout, design, categories, patterns, and more to and showcase your talent. Design and pictures provided are available as source of ideas.

Target Market(s)

Age: 21+ / Family Oriented / Medical Sector / Metropolitan Area / Educated and non Educated Users

Industry/Entity Type

Health Care

Number of Pages Required

5+ page

Font styles to use
Sans Serif

Colors

Designer to choose colors to be used in the design.

Requirements
Must have
• Thin layer design
• Simple font - No serif
• Clean menu with light but solid colors (No Gradient effect)
Nice to have
• Different color themes (2 or 3) can be combined
• Sample pictures for illustration (either as an ad or to go with the flow of your design)
• Dashboard Feel (Suggested but not required)
Should not have
• Artistic fonts - with Serif
• Dark color themes

```html
<!DOCTYPE html>
<html lang="en">
<head>
<meta charset="utf-8">
<title>Corvale — Health Management</title>
<link href="https://fonts.googleapis.com/css2?family=Poppins:wght@500;600;700;800&family=Open+Sans:wght@400;600;700&display=swap" rel="stylesheet">
<style>
:root{
  --blue:#1b5fc4;
  --blue-deep:#1652ad;
  --navy:#1c2440;
  --ink:#2e3140;
  --muted:#55586a;
  --orange:#f5861f;
  --lavender:#eeeef8;
  --lavender-2:#f4f4fb;
  --white:#ffffff;
  --footer:#2a2a2c;
  --footer-text:#cfd0d6;
}
*{margin:0;padding:0;box-sizing:border-box}
html,body{width:1200px;height:4337px;overflow:hidden}
body{position:relative;font-family:"Open Sans",Arial,sans-serif;color:var(--ink);background:var(--white)}
h1,h2,h3{font-family:"Poppins",Arial,sans-serif}
.dash{display:flex;gap:6px}
.dash span{display:block;width:12px;height:3px;background:var(--blue)}
.dash.center{justify-content:center}
.btn{position:absolute;background:var(--orange);color:var(--white);font-family:"Poppins",Arial,sans-serif;font-weight:600;font-size:13px;letter-spacing:.5px;display:flex;align-items:center;justify-content:center;text-transform:uppercase}

/* header */
.site-header{position:absolute;left:0;top:0;width:1200px;height:87px;background:rgba(255,255,255,.72);z-index:5}
.logo{font-family:"Poppins",Arial,sans-serif;font-weight:700;color:var(--blue)}
.site-header .logo{position:absolute;left:145px;top:22px;font-size:30px}
.main-nav{position:absolute;left:399px;top:34px;font-family:"Poppins",Arial,sans-serif;font-size:13px;font-weight:600;color:var(--navy)}
.main-nav a{position:absolute;white-space:nowrap;color:inherit;text-decoration:none}
.main-nav a.active{color:var(--blue)}
.member-login{position:absolute;left:824px;top:28px;width:110px;height:32px;border:2px solid var(--blue);background:#fff;color:var(--blue);font-family:"Poppins",Arial,sans-serif;font-size:11px;font-weight:600;display:flex;align-items:center;justify-content:center}
.lang{position:absolute;left:946px;top:28px;width:63px;height:32px;border:1px solid #c8c9d4;background:#fff;display:flex;align-items:center;justify-content:center;gap:8px}
.lang .flag{width:24px;height:14px;background:#c9d2e6;border:1px solid #9aa3bd}
.search{position:absolute;left:1052px;top:28px;width:116px;height:32px;border:1px solid #c8c9d4;background:#fff;font-size:10px;font-weight:600;color:var(--navy);display:flex;align-items:center;justify-content:space-between;padding:0 10px}

/* hero */
.hero{position:absolute;left:0;top:0;width:1200px;height:694px}
.hero-photo{position:absolute;inset:0;background:
  radial-gradient(ellipse 170px 260px at 230px 430px,#f7f7f9 0%,rgba(247,247,249,0) 100%),
  radial-gradient(ellipse 90px 110px at 230px 250px,#6a4a3c 0%,rgba(106,74,60,0) 100%),
  radial-gradient(ellipse 80px 90px at 520px 200px,#e7e8ee 0%,rgba(231,232,238,0) 100%),
  radial-gradient(ellipse 190px 230px at 520px 420px,#7f97c8 0%,rgba(127,151,200,0) 100%),
  radial-gradient(ellipse 230px 120px at 520px 610px,#4a4d58 0%,rgba(74,77,88,0) 100%),
  radial-gradient(ellipse 120px 200px at 860px 440px,#f4f4f6 0%,rgba(244,244,246,0) 100%),
  radial-gradient(ellipse 150px 80px at 1080px 570px,#cdd3e2 0%,rgba(205,211,226,0) 100%),
  linear-gradient(100deg,#d8d5dc 0%,#cfd0da 40%,#ecebf0 62%,#f3f3f6 80%,#e0e2ea 100%)}
.hero-line{position:absolute;left:717px;top:121px;width:4px;height:197px;background:var(--blue)}
.hero h1{position:absolute;left:757px;top:122px;font-size:38px;line-height:42px;font-weight:800;color:var(--navy);letter-spacing:.5px}
.hero p{position:absolute;left:757px;top:212px;width:360px;font-size:14px;line-height:20px;color:var(--muted)}
.hero .btn{left:757px;top:269px;width:191px;height:40px}
.hero-dots{position:absolute;left:545px;top:643px;display:flex;gap:11px}
.hero-dots span{width:9px;height:9px;border-radius:50%;background:#fff}
.hero-dots span.on{background:var(--orange)}

/* services */
.services{position:absolute;left:0;top:694px;width:1200px;height:752px;background:var(--lavender)}
.section-title{font-family:"Poppins",Arial,sans-serif;font-weight:700;font-size:32px;color:var(--navy)}
.services .section-title{position:absolute;left:0;width:1200px;top:48px;text-align:center}
.services .dash{position:absolute;left:0;width:1200px;top:106px}
.service-card{position:absolute;width:419px;height:240px;background:var(--white);overflow:hidden;box-shadow:0 4px 14px rgba(40,40,90,.06)}
.service-card .blob{position:absolute;left:-70px;top:-70px;width:250px;height:250px;border-radius:50%;background:var(--lavender-2)}
.service-card svg.icon{position:absolute;left:28px;top:34px}
.service-card h3{position:absolute;left:179px;top:34px;font-size:17px;font-weight:500;color:var(--navy)}
.service-card ul{position:absolute;left:179px;top:72px;list-style:none;font-size:13px;line-height:22px;color:var(--muted)}
.service-card li{padding-left:16px;position:relative}
.service-card li::before{content:"";position:absolute;left:2px;top:8px;border-left:6px solid var(--blue);border-top:3.5px solid transparent;border-bottom:3.5px solid transparent}
.service-card .go{position:absolute;right:0;bottom:0}

/* welcome */
.welcome{position:absolute;left:0;top:1446px;width:1200px;height:636px;background:var(--white)}
.welcome-frame{position:absolute;left:145px;top:64px;width:436px;height:509px;background:#e7e7ee;padding:14px}
.welcome-photo{width:100%;height:100%;background:
  radial-gradient(ellipse 80px 120px at 110px 200px,#7fd0ea 0%,rgba(127,208,234,0) 100%),
  radial-gradient(ellipse 140px 90px at 250px 330px,#c79e86 0%,rgba(199,158,134,0) 100%),
  radial-gradient(ellipse 150px 70px at 180px 380px,#2f3c4c 0%,rgba(47,60,76,0) 100%),
  radial-gradient(ellipse 120px 200px at 340px 150px,#f2f4f7 0%,rgba(242,244,247,0) 100%),
  radial-gradient(ellipse 160px 120px at 330px 420px,#e9ecf0 0%,rgba(233,236,240,0) 100%),
  linear-gradient(150deg,#a9bccd 0%,#5c87a8 38%,#8aa6bd 62%,#dfe4ea 100%)}
.welcome .kicker{position:absolute;left:636px;top:108px;font-family:"Poppins",Arial,sans-serif;font-size:20px;font-weight:500;color:var(--navy);letter-spacing:1px}
.welcome .big-logo{position:absolute;left:634px;top:130px;font-size:56px;line-height:70px}
.welcome .dash{position:absolute;left:636px;top:205px}
.welcome p{position:absolute;left:636px;top:246px;width:424px;font-size:14px;line-height:21px;color:var(--muted)}
.welcome .btn{left:636px;top:460px;width:142px;height:46px}

/* tips */
.tips{position:absolute;left:0;top:2082px;width:1200px;height:564px;background:#eeeef7}
.tips-photo{position:absolute;left:480px;top:0;width:720px;height:564px;background:
  radial-gradient(ellipse 90px 150px at 560px 110px,#3a3a3e 0%,rgba(58,58,62,0) 100%),
  radial-gradient(ellipse 200px 120px at 330px 260px,#ffffff 0%,rgba(255,255,255,0) 100%),
  radial-gradient(ellipse 110px 70px at 280px 230px,#8a8a90 0%,rgba(138,138,144,0) 100%),
  radial-gradient(ellipse 140px 90px at 430px 440px,#bdbdc2 0%,rgba(189,189,194,0) 100%),
  radial-gradient(ellipse 160px 250px at 620px 300px,#f6f6f7 0%,rgba(246,246,247,0) 100%),
  linear-gradient(90deg,rgba(238,238,247,1) 0%,rgba(224,224,230,.9) 18%,#d2d2d8 45%,#e4e4e8 75%,#f2f2f4 100%)}
.block-title{position:absolute;font-family:"Poppins",Arial,sans-serif;font-weight:700;font-size:32px;color:var(--navy)}
.ticks{position:absolute;list-style:none;font-size:14px;line-height:31px;color:var(--ink)}
.ticks li{display:flex;align-items:center;gap:12px}
.tips .block-title{left:145px;top:62px}
.tips .dash{position:absolute;left:145px;top:113px}
.tips p{position:absolute;left:145px;top:143px;width:400px;font-size:14px;line-height:21px;color:var(--muted)}
.tips .ticks{left:145px;top:256px}
.tips .btn{left:145px;top:449px;width:142px;height:46px}

/* help */
.help{position:absolute;left:0;top:2646px;width:1200px;height:674px;background:var(--white)}
.help-photo{position:absolute;left:145px;top:78px;width:636px;height:483px;background:
  radial-gradient(ellipse 260px 110px at 330px 40px,#7d9fd4 0%,rgba(125,159,212,0) 100%),
  radial-gradient(ellipse 180px 80px at 120px 110px,#243247 0%,rgba(36,50,71,0) 100%),
  radial-gradient(ellipse 120px 70px at 170px 200px,#c9a08c 0%,rgba(201,160,140,0) 100%),
  radial-gradient(ellipse 260px 130px at 150px 300px,#f3f4f7 0%,rgba(243,244,247,0) 100%),
  radial-gradient(ellipse 110px 70px at 430px 350px,#c69a6a 0%,rgba(198,154,106,0) 100%),
  radial-gradient(ellipse 90px 60px at 500px 330px,#6b3f78 0%,rgba(107,63,120,0) 100%),
  linear-gradient(120deg,#a8b8cf 0%,#d8dee7 40%,#eef0f3 70%,#e2e5ea 100%)}
.help-bar{position:absolute;left:685px;top:124px;width:18px;height:440px;background:var(--blue)}
.help-panel{position:absolute;left:703px;top:124px;width:400px;height:440px;background:var(--white)}
.play{position:absolute;left:421px;top:291px}
.help .block-title{left:740px;top:160px}
.help .dash{position:absolute;left:740px;top:211px}
.help p{position:absolute;left:740px;top:232px;width:330px;font-size:14px;line-height:21px;color:var(--muted)}
.help .ticks{left:740px;top:348px}
.help .btn{left:740px;top:535px;width:142px;height:46px}

/* contact */
.contact{position:absolute;left:0;top:3320px;width:1200px;height:657px;background:var(--blue-deep)}
.contact .section-title{position:absolute;left:0;width:1200px;top:50px;text-align:center;color:var(--white)}
.contact .dash{position:absolute;left:0;width:1200px;top:108px}
.contact .dash span{background:var(--white)}
.map{position:absolute;left:145px;top:165px;width:668px;height:428px;background:
  radial-gradient(ellipse 140px 90px at 90px 330px,#cfe3c4 0%,rgba(207,227,196,0) 100%),
  radial-gradient(ellipse 120px 80px at 560px 80px,#d2e4c8 0%,rgba(210,228,200,0) 100%),
  radial-gradient(ellipse 160px 100px at 380px 250px,#f3ecd9 0%,rgba(243,236,217,0) 100%),
  radial-gradient(ellipse 90px 140px at 620px 330px,#c9daea 0%,rgba(201,218,234,0) 100%),
  radial-gradient(ellipse 120px 70px at 250px 90px,#f1dfc8 0%,rgba(241,223,200,0) 100%),
  linear-gradient(135deg,#ebe8e1 0%,#e6e9e0 40%,#ece8de 70%,#e1e7ec 100%)}
.contact-card{position:absolute;left:656px;top:214px;width:402px;height:318px;background:var(--white);box-shadow:0 8px 24px rgba(0,0,0,.18)}
.contact-row{position:absolute;left:40px;width:340px;display:flex;gap:20px;align-items:center}
.contact-row .ico{flex:none;width:36px;height:36px;border-radius:50%;background:var(--orange);display:flex;align-items:center;justify-content:center}
.contact-row .label{font-size:14px;line-height:19px;color:var(--navy);font-weight:600;text-transform:uppercase}
.contact-row .value{font-size:22px;line-height:26px;color:var(--navy);font-weight:400}
.contact-card hr{position:absolute;left:40px;width:322px;border:0;border-top:1px solid #dfe0e8}

/* footer */
.site-footer{position:absolute;left:0;top:3977px;width:1200px;height:360px;background:var(--footer)}
.site-footer .logo{position:absolute;left:145px;top:103px;font-size:54px}
.foot-col{position:absolute;top:57px}
.foot-col h4{font-family:"Poppins",Arial,sans-serif;font-size:12px;font-weight:600;color:var(--white);letter-spacing:.5px;margin-bottom:12px}
.foot-col ul{list-style:none;font-size:11px;line-height:18px;color:var(--footer-text);text-transform:uppercase}
.social li{display:flex;align-items:center;gap:10px;text-transform:none;line-height:38px}
.social .dot{width:22px;height:22px;border-radius:50%;background:var(--blue)}
.copyright{position:absolute;left:0;width:1200px;top:303px;text-align:center;font-size:11px;color:var(--footer-text)}
</style>
</head>
<body>

<section class="hero">
  <div class="hero-photo" role="img" aria-label="Photograph of a smiling doctor beside a senior patient in a wheelchair, with a nurse and patient in a bright hospital room behind"></div>
  <div class="hero-line"></div>
  <h1>HEALTH<br>MANAGEMENT</h1>
  <p>Sed ut perspiciatis unde omnis iste natus error sit voluptatem accusantium doloremque.</p>
  <div class="btn">
    <svg width="16" height="16" viewBox="0 0 16 16" style="margin-right:8px"><circle cx="7" cy="7" r="5" fill="none" stroke="#fff" stroke-width="2"/><line x1="11" y1="11" x2="15" y2="15" stroke="#fff" stroke-width="2"/></svg>
    Find a doctor
  </div>
  <div class="hero-dots"><span></span><span></span><span class="on"></span><span></span><span></span></div>
</section>

<header class="site-header">
  <div class="logo">Corvale</div>
  <nav class="main-nav">
    <a class="active" style="left:0">HOME</a>
    <a style="left:69px">ABOUT US</a>
    <a style="left:168px">SERVICES</a>
    <a style="left:260px">TIPS</a>
    <a style="left:321px">CONTACT US</a>
  </nav>
  <div class="member-login">MEMBER LOGIN</div>
  <div class="lang"><span class="flag"></span>
    <svg width="10" height="6" viewBox="0 0 10 6"><path d="M1 1l4 4 4-4" fill="none" stroke="#1c2440" stroke-width="1.6"/></svg>
  </div>
  <div class="search"><span>SEARCH</span>
    <svg width="12" height="12" viewBox="0 0 12 12"><circle cx="5" cy="5" r="3.6" fill="none" stroke="#1c2440" stroke-width="1.5"/><line x1="8" y1="8" x2="11" y2="11" stroke="#1c2440" stroke-width="1.5"/></svg>
  </div>
</header>

<section class="services">
  <h2 class="section-title">OUR SERVICES</h2>
  <div class="dash center"><span style="background:var(--orange)"></span><span></span></div>

  <article class="service-card" style="left:165px;top:159px">
    <div class="blob"></div>
    <svg class="icon" width="70" height="80" viewBox="0 0 70 80"><rect x="14" y="10" width="44" height="62" rx="3" fill="none" stroke="#1b5fc4" stroke-width="3"/><rect x="26" y="5" width="20" height="10" rx="2" fill="#f5861f"/><path d="M22 30l4 4 7-8M22 46l4 4 7-8" fill="none" stroke="#f5861f" stroke-width="3"/><line x1="38" y1="31" x2="50" y2="31" stroke="#1b5fc4" stroke-width="3"/><line x1="38" y1="47" x2="50" y2="47" stroke="#1b5fc4" stroke-width="3"/><line x1="22" y1="61" x2="50" y2="61" stroke="#1b5fc4" stroke-width="3"/></svg>
    <h3>Practice Management</h3>
    <ul><li>Lorem ipsum dolor sit</li><li>Sed ut perspiciatis unde</li><li>But I must explain to you</li><li>At vero eos et accusamu</li><li>Coluptatem accusantium</li></ul>
    <svg class="go" width="58" height="58" viewBox="0 0 58 58"><circle cx="29" cy="29" r="21" fill="#f5861f"/><path d="M26 21l8 8-8 8" fill="none" stroke="#fff" stroke-width="3"/></svg>
  </article>

  <article class="service-card" style="left:610px;top:159px">
    <div class="blob"></div>
    <svg class="icon" width="80" height="80" viewBox="0 0 80 80"><rect x="8" y="14" width="50" height="34" rx="3" fill="none" stroke="#1b5fc4" stroke-width="3"/><path d="M18 48l-4 12 14-12" fill="none" stroke="#1b5fc4" stroke-width="3"/><rect x="38" y="32" width="34" height="24" rx="3" fill="#fff" stroke="#f5861f" stroke-width="3"/><path d="M62 56l4 10-12-10" fill="none" stroke="#f5861f" stroke-width="3"/><circle cx="22" cy="31" r="2.5" fill="#f5861f"/><circle cx="31" cy="31" r="2.5" fill="#f5861f"/></svg>
    <h3>Consulting</h3>
    <ul><li>Lorem ipsum dolor sit</li><li>Sed ut perspiciatis unde</li><li>But I must explain to you</li><li>At vero eos et accusamu</li><li>Coluptatem accusantium</li></ul>
    <svg class="go" width="58" height="58" viewBox="0 0 58 58"><circle cx="29" cy="29" r="21" fill="#f5861f"/><path d="M26 21l8 8-8 8" fill="none" stroke="#fff" stroke-width="3"/></svg>
  </article>

  <article class="service-card" style="left:165px;top:434px">
    <div class="blob"></div>
    <svg class="icon" width="70" height="80" viewBox="0 0 70 80"><rect x="12" y="8" width="44" height="62" rx="3" fill="none" stroke="#1b5fc4" stroke-width="3"/><line x1="20" y1="20" x2="48" y2="20" stroke="#1b5fc4" stroke-width="3"/><line x1="20" y1="29" x2="40" y2="29" stroke="#1b5fc4" stroke-width="3"/><circle cx="34" cy="48" r="10" fill="none" stroke="#f5861f" stroke-width="3"/><path d="M29 48l4 4 6-7" fill="none" stroke="#f5861f" stroke-width="3"/></svg>
    <h3>Medical Billing</h3>
    <ul><li>Lorem ipsum dolor sit</li><li>Sed ut perspiciatis unde</li><li>But I must explain to you</li><li>At vero eos et accusamu</li><li>Coluptatem accusantium</li></ul>
    <svg class="go" width="58" height="58" viewBox="0 0 58 58"><circle cx="29" cy="29" r="21" fill="#f5861f"/><path d="M26 21l8 8-8 8" fill="none" stroke="#fff" stroke-width="3"/></svg>
  </article>

  <article class="service-card" style="left:610px;top:434px">
    <div class="blob"></div>
    <svg class="icon" width="80" height="80" viewBox="0 0 80 80"><rect x="14" y="44" width="9" height="22" fill="#f5861f"/><rect x="29" y="34" width="9" height="32" fill="#f5861f"/><rect x="44" y="40" width="9" height="26" fill="#f5861f"/><rect x="59" y="24" width="9" height="42" fill="#f5861f"/><path d="M12 36l18-14 14 8 24-18" fill="none" stroke="#1b5fc4" stroke-width="3"/><line x1="8" y1="68" x2="72" y2="68" stroke="#1b5fc4" stroke-width="3"/></svg>
    <h3>Practice Analysis</h3>
    <ul><li>Lorem ipsum dolor sit</li><li>Sed ut perspiciatis unde</li><li>But I must explain to you</li><li>At vero eos et accusamu</li><li>Coluptatem accusantium</li></ul>
    <svg class="go" width="58" height="58" viewBox="0 0 58 58"><circle cx="29" cy="29" r="21" fill="#f5861f"/><path d="M26 21l8 8-8 8" fill="none" stroke="#fff" stroke-width="3"/></svg>
  </article>
</section>

<section class="welcome">
  <div class="welcome-frame">
    <div class="welcome-photo" role="img" aria-label="Photograph of a doctor's hands using a tablet showing a glowing body scan"></div>
  </div>
  <div class="kicker">WELCOME TO</div>
  <div class="logo big-logo">Corvale</div>
  <div class="dash"><span></span><span></span></div>
  <p>On the other hand, we denounce with righteous indignation and dislike men who are so beguiled and demoralized by the charms of pleasure of the moment, so blinded by desire, that they cannot foresee the pain and trouble that are bound to ensue; and equal blame belongs to those who fail in their duty through weakness of will, which is the same as saying through shrinking from toil and pain. These cases are perfectly simple.</p>
  <div class="btn">Read more</div>
</section>

<section class="tips">
  <div class="tips-photo" role="img" aria-label="Black and white photograph of a doctor with a stethoscope writing on a clipboard"></div>
  <h2 class="block-title">HEALTH TIPS</h2>
  <div class="dash"><span></span><span></span></div>
  <p>On the other hand, we denounce with right eous indignation and dislike men who are so beguiled and demoralized by the charms of pleasure of the moment</p>
  <ul class="ticks">
    <li><svg width="16" height="16" viewBox="0 0 16 16"><circle cx="8" cy="8" r="8" fill="#1b5fc4"/><path d="M4.5 8.2l2.4 2.3 4.6-4.8" fill="none" stroke="#fff" stroke-width="1.8"/></svg>Lorem Ipsum is simply dummy text</li>
    <li><svg width="16" height="16" viewBox="0 0 16 16"><circle cx="8" cy="8" r="8" fill="#1b5fc4"/><path d="M4.5 8.2l2.4 2.3 4.6-4.8" fill="none" stroke="#fff" stroke-width="1.8"/></svg>There are many variations of</li>
    <li><svg width="16" height="16" viewBox="0 0 16 16"><circle cx="8" cy="8" r="8" fill="#1b5fc4"/><path d="M4.5 8.2l2.4 2.3 4.6-4.8" fill="none" stroke="#fff" stroke-width="1.8"/></svg>It is a long established fact</li>
    <li><svg width="16" height="16" viewBox="0 0 16 16"><circle cx="8" cy="8" r="8" fill="#1b5fc4"/><path d="M4.5 8.2l2.4 2.3 4.6-4.8" fill="none" stroke="#fff" stroke-width="1.8"/></svg>Sed ut perspiciatis unde omnis</li>
    <li><svg width="16" height="16" viewBox="0 0 16 16"><circle cx="8" cy="8" r="8" fill="#1b5fc4"/><path d="M4.5 8.2l2.4 2.3 4.6-4.8" fill="none" stroke="#fff" stroke-width="1.8"/></svg>Lorem ipsum dolor sit amet</li>
  </ul>
  <div class="btn">Read more</div>
</section>

<section class="help">
  <div class="help-photo" role="img" aria-label="Photograph of a doctor typing on a laptop beside a stethoscope and clipboard"></div>
  <svg class="play" width="72" height="72" viewBox="0 0 72 72"><circle cx="36" cy="36" r="34" fill="#f5861f" stroke="#fff" stroke-width="3"/><path d="M29 22l22 14-22 14z" fill="#fff"/></svg>
  <div class="help-bar"></div>
  <div class="help-panel"></div>
  <h2 class="block-title">HELP</h2>
  <div class="dash"><span></span><span></span></div>
  <p>On the other hand, we denounce with right eous indignation and dislike men who are so beguiled and demoralized by the charms of pleasure of the moment</p>
  <ul class="ticks">
    <li><svg width="16" height="16" viewBox="0 0 16 16"><circle cx="8" cy="8" r="8" fill="#1b5fc4"/><path d="M4.5 8.2l2.4 2.3 4.6-4.8" fill="none" stroke="#fff" stroke-width="1.8"/></svg>Lorem Ipsum is simply dummy text</li>
    <li><svg width="16" height="16" viewBox="0 0 16 16"><circle cx="8" cy="8" r="8" fill="#1b5fc4"/><path d="M4.5 8.2l2.4 2.3 4.6-4.8" fill="none" stroke="#fff" stroke-width="1.8"/></svg>There are many variations of</li>
    <li><svg width="16" height="16" viewBox="0 0 16 16"><circle cx="8" cy="8" r="8" fill="#1b5fc4"/><path d="M4.5 8.2l2.4 2.3 4.6-4.8" fill="none" stroke="#fff" stroke-width="1.8"/></svg>It is a long established fact</li>
    <li><svg width="16" height="16" viewBox="0 0 16 16"><circle cx="8" cy="8" r="8" fill="#1b5fc4"/><path d="M4.5 8.2l2.4 2.3 4.6-4.8" fill="none" stroke="#fff" stroke-width="1.8"/></svg>Sed ut perspiciatis unde omnis</li>
    <li><svg width="16" height="16" viewBox="0 0 16 16"><circle cx="8" cy="8" r="8" fill="#1b5fc4"/><path d="M4.5 8.2l2.4 2.3 4.6-4.8" fill="none" stroke="#fff" stroke-width="1.8"/></svg>Lorem ipsum dolor sit amet</li>
  </ul>
  <div class="btn">Read more</div>
</section>

<section class="contact">
  <h2 class="section-title">CONTACT US</h2>
  <div class="dash center"><span></span><span></span></div>
  <div class="map" role="img" aria-label="Street map of the city centre with a location marker at the office"></div>
  <div class="contact-card">
    <div class="contact-row" style="top:38px">
      <span class="ico"><svg width="14" height="18" viewBox="0 0 14 18"><path d="M7 1a6 6 0 0 0-6 6c0 4.5 6 10 6 10s6-5.5 6-10a6 6 0 0 0-6-6z" fill="#fff"/><circle cx="7" cy="7" r="2.2" fill="#f5861f"/></svg></span>
      <div class="label">2240 Linden Crest Road<br>Brookvale, WA 98000</div>
    </div>
    <hr style="top:106px">
    <div class="contact-row" style="top:130px">
      <span class="ico"><svg width="16" height="16" viewBox="0 0 16 16"><path d="M3 1l3 .5 1 3.5-2 1.5a9 9 0 0 0 4.5 4.5l1.5-2 3.5 1 .5 3-2 2C7 15 1 9 1 3z" fill="#fff"/></svg></span>
      <div><div class="label" style="font-weight:400">Call us</div><div class="value">555.010.2200</div></div>
    </div>
    <hr style="top:200px">
    <div class="contact-row" style="top:224px">
      <span class="ico"><svg width="16" height="12" viewBox="0 0 16 12"><rect x="0.5" y="0.5" width="15" height="11" rx="1" fill="#fff"/><path d="M1 1l7 6 7-6" fill="none" stroke="#f5861f" stroke-width="1.5"/></svg></span>
      <div><div class="label" style="font-weight:400">E mail us</div><div class="value">info@corvale.com</div></div>
    </div>
  </div>
</section>

<footer class="site-footer">
  <div class="logo">Corvale</div>
  <div class="foot-col" style="left:512px">
    <h4>MENU</h4>
    <ul><li>Home</li><li>About us</li><li>Services</li><li>Tips</li><li>Contact us</li></ul>
  </div>
  <div class="foot-col" style="left:708px">
    <h4>GLOSSARY</h4>
    <ul><li>Biometrics</li><li>Allergies</li><li>Illnesses</li><li>Medications</li><li>Medical procedures</li><li>Doctors</li></ul>
  </div>
  <div class="foot-col" style="left:934px">
    <h4>CONNECT WITH US</h4>
    <ul class="social" style="margin-top:-6px">
      <li><span class="dot"></span>Facepage</li>
      <li><span class="dot"></span>Chirper</li>
      <li><span class="dot"></span>Linkwork</li>
    </ul>
  </div>
  <div class="copyright">Copyright @ 2019 All Rights Reserved</div>
</footer>

</body>
</html>
```